Business Card Design for the Harborline Vascular and Brightmere Aesthetic Institute Clinics

We need one business card design for an existing company based in Chicago called Harborline Vascular Institute and Brightmere Aesthetic Institute. We are vein and plastic surgery clinics. There are two speared logos for each company Harborline Vascular and Brightmere Aesthetic Institute.Before we had two separate busniess cards for each company, but now we want to combained them into one, and thus the both logos need to be on the the card. I would like to see the design that follow the design of our brochure and folders. The colors included need to be the ones of our two logos(orange, gray and teal--> see the attachment). The design needs to represent two companies under one roof. The final design should communicate trust and loyalty

Target Market(s)

Medical

Industry/Entity Type

Medical

Contact Information for Business Card

Harborline Vascular InstituteBrightmere Aesthetic Institute4817 N. Tallow Creek Ave. Chicago, IL 60618www.harborlinevascular.examplewww.brightmereaesthetic.exampleTelephone (773) 555-0182Fax (773) 555-0183

Requirements
Must have
• Both logos, ultimately representing both companies at one card

```html
<!DOCTYPE html>
<html lang="en">
<head>
<meta charset="utf-8">
<title>Harborline Vascular &amp; Brightmere Aesthetic – Business Card</title>
<link href="https://fonts.googleapis.com/css2?family=Karla:wght@400;500;700&display=swap" rel="stylesheet">
<style>
  :root {
    --orange: #e5771b;
    --gray: #a3a3a3;
    --teal: #1d6870;
    --ink: #262626;
    --white: #ffffff;
    --backdrop: #ece9e4;
  }
  * { box-sizing: border-box; margin: 0; padding: 0; }
  html, body { width: 1200px; height: 1200px; overflow: hidden; }
  body {
    background: var(--backdrop);
    font-family: "Karla", Arial, sans-serif;
    position: relative;
  }
  .card {
    position: absolute;
    left: 150px;
    width: 900px;
    height: 520px;
    box-shadow: 0 10px 30px rgba(0,0,0,0.18);
    overflow: hidden;
  }
  .card--front { top: 60px; background: var(--orange); }
  .card--back { top: 620px; background: var(--white); }

  /* Vascular wordmark: dot above, rule, name below, rule spans the name */
  .vein-mark {
    position: absolute;
    display: inline-block;
  }
  .vein-mark__dot {
    position: absolute;
    right: 6px;
    top: -46px;
    width: 16px; height: 16px;
    border-radius: 50%;
    background: var(--teal);
  }
  .vein-mark__rule {
    display: block;
    width: 100%;
    height: 2px;
    background: var(--teal);
    margin-bottom: 7px;
  }
  .vein-mark__name {
    display: block;
    color: var(--gray);
    font-weight: 700;
    letter-spacing: 1.5px;
    text-transform: uppercase;
    white-space: nowrap;
    line-height: 1;
  }

  /* Aesthetic wordmark */
  .aesthetic-mark { position: absolute; }
  .aesthetic-mark__dot {
    width: 18px; height: 18px;
    border-radius: 50%;
    background: var(--orange);
  }
  .aesthetic-mark__name {
    color: var(--orange);
    font-weight: 400;
    text-transform: uppercase;
    letter-spacing: 3px;
    line-height: 1.3;
  }

  /* Front */
  .card--front .vein-mark { left: 42px; top: 235px; }
  .card--front .vein-mark__name { font-size: 20px; }
  .logo-panel {
    position: absolute;
    left: 440px; top: 75px;
    width: 370px; height: 370px;
    background: var(--white);
    display: flex; align-items: center; justify-content: center;
  }
  .logo-panel .aesthetic-mark {
    position: static;
    display: flex; flex-direction: column; align-items: center;
    text-align: center;
  }
  .logo-panel .aesthetic-mark__dot { margin-bottom: 22px; }
  .logo-panel .aesthetic-mark__name { font-size: 22px; }

  /* Back */
  .accent-bar {
    position: absolute;
    left: 0; top: 88px;
    width: 66px; height: 352px;
    background: var(--orange);
  }
  .card--back .aesthetic-mark { left: 97px; top: 90px; }
  .card--back .aesthetic-mark__dot { margin-bottom: 82px; }
  .card--back .aesthetic-mark__name { font-size: 18px; letter-spacing: 2.5px; line-height: 1.25; }
  .web-list {
    position: absolute;
    right: 64px; top: 200px;
    text-align: right;
    list-style: none;
    font-size: 23px;
    line-height: 1.4;
    color: var(--ink);
  }
  .address {
    position: absolute;
    left: 97px; top: 322px;
    font-style: normal;
    font-size: 23px;
    line-height: 1.4;
    color: var(--ink);
  }
  .address b { font-weight: 700; }
  .card--back .vein-mark { right: 64px; top: 404px; }
  .card--back .vein-mark__name { font-size: 22px; }
</style>
</head>
<body>

<section class="card card--front" aria-label="Card front">
  <div class="vein-mark">
    <span class="vein-mark__dot"></span>
    <span class="vein-mark__rule"></span>
    <span class="vein-mark__name">Harborline Vascular Institute</span>
  </div>
  <div class="logo-panel">
    <div class="aesthetic-mark">
      <div class="aesthetic-mark__dot"></div>
      <div class="aesthetic-mark__name">Brightmere<br>Aesthetic<br>Institute</div>
    </div>
  </div>
</section>

<section class="card card--back" aria-label="Card back">
  <div class="accent-bar"></div>
  <div class="aesthetic-mark">
    <div class="aesthetic-mark__dot"></div>
    <div class="aesthetic-mark__name">Brightmere<br>Aesthetic<br>Institute</div>
  </div>
  <ul class="web-list">
    <li>www.harborlinevascular.example</li>
    <li>www.brightmereaesthetic.example</li>
  </ul>
  <address class="address">
    4817 N. Tallow Creek Ave.<br>
    Lakeport, IL 60699<br>
    <b>T:</b> (773) 555-0182,<br>
    <b>F:</b> (773) 555-0183
  </address>
  <div class="vein-mark">
    <span class="vein-mark__dot"></span>
    <span class="vein-mark__rule"></span>
    <span class="vein-mark__name">Harborline Vascular Institute</span>
  </div>
</section>

</body>
</html>
```